Kelumo.cn needs pages to be re-designed

www.kelumo.cn is our current new site which was launched in April.
We're a financial services website in the crowdfunding space in China to connect borrower's and lender's.

test.kelumo.cn is our test site
u: test
p: newtest
http://test.kelumo.cn/
http://test.kelumo.cn/user/accounts/new_lender
http://test.kelumo.cn/user/accounts/new_borrower
http://test.kelumo.cn/introductions/protection
http://test.kelumo.cn/introductions
http://test.kelumo.cn/introductions/kelumo_admin
http://test.kelumo.cn/introductions/contact
Some of the pages have pop-ups in the bloc's of the pages. Please click the links, to see more content.

User's currently criticize the website for being:
- Too Western looking
- Too simple, too little content
- Content NOT in the pop-ups are too simple
- Pictures are too big and too much blank space
- Relevant information is not there when needed
- The pictures are too generic

What we would like to do is re-design those pages with the same color scheme and style to be more compelling, efficient, non-intimidating and easy-to-use. Our audience is Ages 25-35 predominantly male investors.
We are looking for more ideas to make the content match the style, while bridging western and chinese design. Our ultimate goal is to increase registrants to the website and highlight our core competitive advantages.

Some competitors websites are:
www.fobuxiqi.com
www.tamev.com
www.zzzlendo.com

Reason: Not enough good designs that follow the prompt. Same style, better information layout!

Reason: Still have not received a design we're satisfied with

Reason: WE DONT WANT A COMPLETE REDESIGN OF PAGES . KEEP THE EXACT SAME COLOR AND STYLE - WE WANT CONTENT RE-DESIGN! THE BLOCS ARE TOO SIMPLE - WE WANT MORE CONTENT INSIDE.

Reason: no new designs

Reason: no new designs

Reason: other non-registered pages need to be re-designed

```html
<!DOCTYPE html>
<html lang="zh-CN">
<head>
<meta charset="utf-8">
<title>常见问题 - Kelumo.cn</title>
<link rel="stylesheet" href="https://fonts.googleapis.com/css2?family=Noto+Sans+SC:wght@400;500;700&display=swap">
<style>
:root{
  --green:#4cae2f;
  --green-text:#5bb53a;
  --ink:#2b2b2b;
  --muted:#8a8a8a;
  --body:#8c8c8c;
  --line:#e3e3e3;
  --side:#f5f5f5;
  --side-line:#e9e9e9;
  --footer:#c9c9c9;
  --footer-icon:#9e9e9e;
  --white:#ffffff;
  --hero-light:#9a9a9a;
  --hero-mid:#6e6e6e;
  --hero-dark:#555555;
}
*{margin:0;padding:0;box-sizing:border-box}
html,body{width:930px;height:1200px;overflow:hidden;background:var(--white)}
body{font-family:"Noto Sans SC","Microsoft YaHei",sans-serif;color:var(--ink);position:relative}

.site-header{position:absolute;left:0;top:0;width:930px;height:71px;background:var(--white)}
.brand{position:absolute;left:67px;top:14px;display:flex;align-items:center;gap:8px}
.brand-dot{width:42px;height:42px;border-radius:50%;background:var(--green)}
.brand-name{font-size:17px;font-weight:500;color:var(--ink)}
.main-nav{position:absolute;right:42px;top:28px;display:flex;gap:28px;font-size:11px;color:var(--ink)}
.main-nav a{color:inherit;text-decoration:none;display:flex;align-items:center;gap:4px}
.main-nav svg{width:12px;height:12px}

.hero{position:absolute;left:0;top:71px;width:930px;height:275px;background:radial-gradient(ellipse at 50% 45%,var(--hero-light) 0%,var(--hero-mid) 55%,var(--hero-dark) 100%)}

.page-title{position:absolute;left:66px;top:379px;font-size:20px;line-height:28px;font-weight:400;color:var(--green-text)}

.sidebar{position:absolute;left:0;top:427px;width:212px;height:717px;background:var(--side)}
.side-nav{list-style:none}
.side-nav li{height:35px;line-height:35px;padding-left:68px;font-size:13px;color:var(--ink);border-bottom:1px solid var(--side-line)}
.side-nav li.active{background:var(--green);color:var(--white);width:215px;height:33px;line-height:33px;position:relative;border-bottom:0}
.side-nav li.active::after{content:"";position:absolute;right:14px;top:13px;border-left:4px solid var(--white);border-top:3px solid transparent;border-bottom:3px solid transparent}

.faq{position:absolute;left:238px;top:421px;width:638px}
.faq-heading{font-size:16px;line-height:22px;font-weight:500;color:var(--ink)}
.faq-sub{font-size:10px;line-height:14px;color:var(--muted);margin-top:2px;padding-bottom:9px;border-bottom:1px solid var(--line)}
.faq-item{font-size:12px;color:var(--ink);height:30.6px;line-height:30.6px;white-space:nowrap}
.faq-item.open{display:flex;justify-content:space-between;margin-top:8px;height:30px;line-height:30px}
.collapse{color:var(--green-text);text-decoration:underline}
.answer{font-size:11.6px;line-height:20.2px;color:var(--body);margin:15px 0 36px}
.answer span{display:block;white-space:nowrap}

.site-footer{position:absolute;left:0;top:1144px;width:930px;height:56px;background:var(--footer)}
.help{position:absolute;left:70px;top:18px;display:flex;align-items:center;gap:8px;color:var(--white);font-size:12px}
.footer-toggle{position:absolute;left:235px;top:20px;font-size:10px;color:var(--ink)}
.social{position:absolute;right:40px;top:14px;display:flex;gap:12px;align-items:center}
.social span{width:24px;height:24px;border-radius:50%;background:var(--footer-icon);display:block}
</style>
</head>
<body>
<header class="site-header">
  <div class="brand"><span class="brand-dot"></span><span class="brand-name">Kelumo.cn</span></div>
  <nav class="main-nav">
    <a href="#"><svg viewBox="0 0 12 12"><circle cx="6" cy="6" r="5" fill="#2b2b2b"/></svg>首页</a>
    <a href="#"><svg viewBox="0 0 12 12"><path d="M6 1 L11 3 V6 C11 9 6 11 6 11 C6 11 1 9 1 6 V3 Z" fill="#2b2b2b"/></svg>安全</a>
    <a href="#"><svg viewBox="0 0 12 12"><path d="M1 4h10v2H1zM1 7h10v2H1z" fill="#2b2b2b"/></svg>投资</a>
    <a href="#"><svg viewBox="0 0 12 12"><rect x="2" y="2" width="8" height="9" fill="none" stroke="#2b2b2b" stroke-width="1.4"/></svg>贷款</a>
    <a href="#"><svg viewBox="0 0 12 12"><rect x="2" y="5" width="8" height="6" fill="#2b2b2b"/><path d="M4 5V3a2 2 0 0 1 4 0v2" fill="none" stroke="#2b2b2b" stroke-width="1.4"/></svg>登录 ▾</a>
  </nav>
</header>

<div class="hero" role="img" aria-label="黑白照片：身穿西装的男子背对镜头，面前墙上画着指向不同方向的白色箭头"></div>

<h1 class="page-title">常见问题</h1>

<aside class="sidebar">
  <ul class="side-nav">
    <li class="active">投资</li>
    <li>贷款</li>
    <li>其他</li>
  </ul>
</aside>

<main class="faq">
  <h2 class="faq-heading">投資常見問題</h2>
  <p class="faq-sub">單擊某個主題，查看有關該主題的幫助文章。</p>
  <div class="faq-item open"><span>1. 注册过程中如有中断，再次进入平台是否可以继续注册过程?</span><a class="collapse">点击收缩</a></div>
  <p class="answer">
    <span>为减少投资风险，可路贷规定投资人在投资借款项目时，每个借款项目只能投资一次，并且只能投资该借款项目额度的</span>
    <span>80%。</span>
    <span>出借资金以后，如果每月账户的还款不足100元，将无法进行再投资，会影响到最终的年化收益，每月满足100元进行</span>
    <span>再投资才可以不断滚动生息达到年化12%-15%的收益。</span>
    <span>投资人发起债权转让只能转让单笔大于100元的债权，低于100元的债权由于系统限制将无法通过。</span>
    <span>如果投资人选择了自动投标，请尽量把投资期限设置成12个月或18个月，这样便于系统平台尽快将您的资金投资出</span>
    <span>去。</span>
    <span>为避免个别信用卡套现投机行为的出现，可路贷规定投资人累计充值1000元以上，且不投资就直接提现的行为会被禁止</span>
    <span>通过，鉴于部分新客户是为了测试平台真实性及提现效率，我们建议测试金额在1000元（含）以内，100元——1000</span>
    <span>元（含）以内的上述行为仍然予以支持。</span>
  </p>
  <div class="faq-item">2. 出借人（或借款人）可不可以再同时注册借款人（或出借人）账户?</div>
  <div class="faq-item">3. 可路贷与其他同类公司的区别是什么?</div>
  <div class="faq-item">4. 如何提供信用等级和信用额度?</div>
  <div class="faq-item">5. 信用等级的高低对用户借款有什么影响?</div>
  <div class="faq-item">6. 加分资料都包括哪些资料?</div>
  <div class="faq-item">7. 注册过程中如有中断，再次进入平台是否可以继续注册过程?</div>
  <div class="faq-item">8. 出借人（或借款人）可不可以再同时注册借款人（或出借人）账户?</div>
  <div class="faq-item">9. 可路贷与其他同类公司的区别是什么?</div>
  <div class="faq-item">10. 如何提供信用等级和信用额度?</div>
  <div class="faq-item">11. 信用等级的高低对用户借款有什么影响?</div>
  <div class="faq-item">12. 加分资料都包括哪些资料?</div>
</main>

<footer class="site-footer">
  <div class="help"><svg width="22" height="20" viewBox="0 0 22 20"><rect x="8" y="1" width="13" height="9" rx="2" fill="#fff"/><circle cx="5" cy="12" r="3" fill="#fff"/><path d="M0 20a5 5 0 0 1 10 0z" fill="#fff"/></svg>我需要帮助</div>
  <div class="footer-toggle">显示页脚信息+</div>
  <div class="social">
    <svg width="26" height="24" viewBox="0 0 26 24"><circle cx="9" cy="7" r="5" fill="#9e9e9e"/><path d="M0 24a9 9 0 0 1 18 0z" fill="#9e9e9e"/><path d="M21 6v8M17 10h8" stroke="#9e9e9e" stroke-width="2.4"/></svg>
    <span></span><span></span><span></span>
  </div>
</footer>
</body>
</html>
```